Elegant Business Card for Technology Company

Client is a supplier of innovative industrial communications and automation equipment since 2002. This contest is to gather fresh ideas for a redesign of the existing business card. Client is looking for design that best communicates tagline "Industrial Networking and Computing Specialist".

Design submissions should look modern, clean, elegant and professional. It should not be cluttered. Use white as the primary colour. Orange and black as secondary colour. Refer to jpeg File 1 on the current design.

Fonts used by Client used include Arial Regular, Arial Black, Roboto Regular, Roboto Black and Lato.

The winning design will be sent for offset printing using super white 250gsm artcard paper (open for suggestions).

Target Market(s)

System Engineers, Project Managers, Purchasing Managers from companies providing engineering services for Smart Cities.

Industry/Entity Type

Information Technology

Contact Information for Business Card

Refer to PDF File 3 for Business Card Details. Priority of short contact information would be as follows Name > Job Title > Email > Mobile > Web > Tel > Fax > Business Address >UEN (UEN represents company registration number)

Font styles to use
Sans Serif

Colors
ffffff
f37122
000000
5c5c5c

Requirements
Must have
• Refer to AI File 2 (Company Logo) & PDF File 3 (Information on Namecard)
Should not have
• No QR codes
• No Social Media Icons
• Do not create full Black or Orange colour background

```html
<!DOCTYPE html>
<html lang="en">
<head>
<meta charset="utf-8">
<title>Norvale Business Card</title>
<link rel="stylesheet" href="https://fonts.googleapis.com/css2?family=Roboto:wght@400;500;700;900&display=swap">
<style>
  :root {
    --white: #ffffff;
    --orange: #f37122;
    --black: #1a1a1a;
    --grey: #5c5c5c;
    --stage-light: #e6e6e6;
    --stage-dark: #7d7d7d;
    --faint: #d9d9d9;
  }
  * { box-sizing: border-box; margin: 0; padding: 0; }
  html, body { width: 1200px; height: 900px; overflow: hidden; }
  body {
    font-family: "Roboto", Arial, sans-serif;
    background: radial-gradient(ellipse at 45% 40%, var(--stage-light) 0%, #b3b3b3 55%, var(--stage-dark) 100%);
    position: relative;
    color: var(--black);
  }
  .card {
    position: absolute;
    width: 560px;
    height: 320px;
    background: linear-gradient(160deg, var(--white) 0%, #f4f4f4 100%);
    box-shadow: 0 8px 22px rgba(0,0,0,0.28);
    overflow: hidden;
  }
  .card--front { left: 80px; top: 100px; }
  .card--back { left: 560px; top: 480px; }

  .brand { display: flex; align-items: center; gap: 10px; flex: none; }
  .brand__dot { width: 58px; height: 58px; border-radius: 50%; background: var(--orange); }
  .brand__name { font-weight: 900; font-size: 38px; letter-spacing: 1px; color: var(--black); line-height: 1; }
  .card--front .brand { position: absolute; left: 150px; top: 44px; }
  .company { position: absolute; left: 218px; top: 92px; font-size: 12px; font-weight: 700; color: var(--black); }

  .rule-dots { position: absolute; border-top: 2px dotted var(--black); }
  .rule-dots--right { left: 430px; right: 0; top: 100px; }
  .rule-dots--left { left: 0; width: 118px; top: 156px; border-color: var(--orange); }

  .identity { position: absolute; left: 130px; top: 140px; display: flex; align-items: center; gap: 12px; }
  .identity__name { color: var(--orange); font-size: 22px; font-weight: 700; }
  .identity__sep { width: 1.5px; height: 22px; background: var(--black); }
  .identity__title { font-size: 13px; color: var(--black); }

  .address { position: absolute; left: 30px; top: 196px; font-size: 13px; color: var(--black); }

  .contacts {
    position: absolute; left: 30px; top: 228px;
    display: grid;
    grid-template-columns: 150px 170px auto;
    row-gap: 6px; column-gap: 16px;
    font-size: 13px;
  }
  .contacts__label { color: var(--orange); font-weight: 700; margin-right: 10px; }

  .back-header {
    position: absolute; left: 28px; right: 0; top: 26px;
    display: flex; align-items: center; gap: 18px;
  }
  .back-rule { flex: 1; height: 3px; background: var(--orange); margin-top: 14px; }
  .back-pattern {
    position: absolute; right: -110px; top: 30px;
    width: 300px; height: 300px; border-radius: 50%;
    background: var(--faint); opacity: 0.6;
  }
  .tagline { position: absolute; left: 190px; top: 96px; font-size: 14px; color: var(--black); }
  .services { position: absolute; left: 170px; top: 132px; list-style: none; font-size: 14px; line-height: 21px; color: var(--black); }
  .services li { position: relative; padding-left: 12px; }
  .services li::before {
    content: ""; position: absolute; left: 0; top: 8px;
    width: 5px; height: 5px; border-radius: 50%; background: var(--orange);
  }
</style>
</head>
<body>
  <section class="card card--front" aria-label="Business card front">
    <div class="brand">
      <span class="brand__dot"></span>
      <span class="brand__name">NORVALE</span>
    </div>
    <p class="company">Norvale Asia Pacific Pte Ltd</p>
    <div class="rule-dots rule-dots--right"></div>
    <div class="rule-dots rule-dots--left"></div>
    <div class="identity">
      <span class="identity__name">Daniel Loh</span>
      <span class="identity__sep"></span>
      <span class="identity__title">Sales Manager</span>
    </div>
    <p class="address">22 Kallang Way Tech Hub #05-12 (Lobby B), Singapore 349001</p>
    <div class="contacts">
      <span><span class="contacts__label">M.</span>+65 9123 4567</span>
      <span><span class="contacts__label">T.</span>+65 6345 2210</span>
      <span><span class="contacts__label">E.</span>+65 6345 2211</span>
      <span><span class="contacts__label">E.</span>hello@norvale.com.sg</span>
      <span><span class="contacts__label">W.</span>www.norvale.com.sg</span>
      <span><span class="contacts__label">UEN No</span>200405117K</span>
    </div>
  </section>

  <section class="card card--back" aria-label="Business card back">
    <div class="back-pattern" role="img" aria-label="Faint grey decorative dot pattern"></div>
    <div class="back-header">
      <div class="brand">
        <span class="brand__dot"></span>
        <span class="brand__name">NORVALE</span>
      </div>
      <div class="back-rule"></div>
    </div>
    <p class="tagline">Industrial Networking and Computing Specialist</p>
    <ul class="services">
      <li>Industrial Ethernet / Wireless / Cellular</li>
      <li>Industrial and Embedded Computing</li>
      <li>Serial / Fieldbus Connectivity</li>
      <li>IP Video Surveillance</li>
      <li>Remote Automation</li>
    </ul>
  </section>
</body>
</html>
```